Web design for Crowdfunding site HopeWingsRally.com

We need a web design for christian crowdfunding website. Here is the challenge: We need responsive layout that is targeted first in iPad size of screen. It should also scale somehow down to iPhone size of screens. Web layout can be about the same size as iPad screen.

Screens should work so that main page scrolls not but only certain part of the screen scrolls and always one "page" at time. We can implement these "scrolls" then later with javascript but now we need only design. The challenge is to create this kind of hybrid website / app look.

Target is at first to raise funds to orphan people needing about $40 per month for their living and education. There is always some organization which takes care of these kids. Later there will be other christian missions included. At first we are looking to find monthly supporters.

You can be as creative as you want :) As you see from the look and feel sector, I am not looking any same traditional look which many "help kids" sites have. I am looking to reach now younger generation and therefore iPad and mobile are the main screen sizes.

Inspirational designs:
- https://example-gallery.test/profiles/studiofernlake/designs/482716?from=%2Fbrowse%2Fxhr%2Fdesigns%3Fcategory%3Dmobile-app-design
- http://www.artpoolhub.test/design/8261047 Clear, simple visuals
- http://www.artpoolhub.test/design/7394215 Header
- http://www.artpoolhub.test/design/6048392 Contrast in the colors, i think is powerfull

Some terms could be: Kids play, kids are learning (in the school). No static posture but living like kids are. I wonder also how we could also add little bit gaming style even though the question is of reali life of real people. Giving should be rewarding.

Target Market(s)

People who want help other people.

Industry/Entity Type

Christian

Number of Pages Required

4 page

Requirements
Must have
• Homepage. Mission page (In my wireframes it was one kid).
Nice to have
• Other pages and some idea how to scroll. 4 pages is no must. If you feel easy, please give first some draft and I give comments on that.

```html
<!DOCTYPE html>
<html lang="en">
<head>
<meta charset="utf-8">
<title>HopeWingsRally – Mission</title>
<link rel="stylesheet" href="https://fonts.googleapis.com/css2?family=Hind:wght@400;500;600&family=Montserrat:wght@500;600&display=swap">
<style>
  :root {
    --ink: #161616;
    --muted: #8f8f8f;
    --gold: #f4a700;
    --red: #e8333a;
    --bar: #f3f3f3;
    --paper: #ffffff;
    --line: #9c9c9c;
  }
  * { box-sizing: border-box; margin: 0; padding: 0; }
  html, body { width: 1200px; height: 935px; overflow: hidden; background: var(--paper); }
  body { font-family: "Hind", Arial, sans-serif; color: var(--ink); position: relative; }

  .topbar {
    position: absolute; left: 0; top: 0; width: 1200px; height: 68px;
    background: var(--bar); display: flex; align-items: center;
  }
  .menu-toggle {
    position: absolute; left: 26px; top: 22px; display: flex; align-items: center; gap: 12px;
    font-family: "Montserrat", Arial, sans-serif; font-weight: 600; font-size: 18px;
    color: #7a7a7a; letter-spacing: 0.3px;
  }
  .brand {
    position: absolute; left: 0; right: 0; top: 14px; text-align: center;
    font-family: "Montserrat", Arial, sans-serif; font-weight: 500; font-size: 38px;
    letter-spacing: 0.5px; color: var(--ink);
  }
  .auth { position: absolute; right: 26px; top: 16px; display: flex; gap: 22px; }
  .auth-btn {
    height: 36px; padding: 0 24px; display: flex; align-items: center;
    font-family: "Montserrat", Arial, sans-serif; font-weight: 600; font-size: 15px;
    color: #fff; text-decoration: none;
  }
  .auth-btn.login { background: var(--ink); }
  .auth-btn.signup { background: var(--red); }

  .hero-photo {
    position: absolute; left: 670px; top: 68px; width: 530px; height: 620px;
    background: linear-gradient(135deg, #d9d9d9 0%, #8a8a8a 45%, #3a3a3a 100%);
    clip-path: polygon(8% 0, 100% 0, 100% 30%, 72% 52%, 62% 100%, 38% 100%, 22% 70%, 0 40%);
  }

  .family-icon { position: absolute; left: 52px; top: 130px; width: 120px; height: 120px; }

  .pledge { position: absolute; left: 30px; top: 278px; }
  .pledge-line { font-size: 58px; font-weight: 500; line-height: 66px; color: var(--ink); }
  .pledge-line .gold { color: var(--gold); }
  .pledge-line .grey { color: var(--muted); }
  .pledge-punch { font-size: 92px; font-weight: 500; line-height: 100px; color: var(--red); margin-top: 6px; }
  .pledge-punch .close { color: var(--ink); }
  .pledge-note { font-size: 36px; font-weight: 500; color: #6f6f6f; margin-top: 0; }

  .footer-strip {
    position: absolute; left: 0; bottom: 0; width: 412px; height: 76px; background: var(--bar);
    display: flex; align-items: center; padding-left: 28px; gap: 8px;
    font-size: 20px; color: var(--ink);
  }
  .footer-strip .mark { color: var(--red); font-size: 22px; }
  .footer-strip a { color: var(--red); text-decoration: none; }
  .page-code { position: absolute; right: 66px; bottom: 36px; font-size: 15px; font-weight: 600; }
</style>
</head>
<body>
  <header class="topbar">
    <div class="menu-toggle">
      <svg width="28" height="20" viewBox="0 0 28 20" aria-hidden="true">
        <rect y="1" width="28" height="3" fill="#8a8a8a"/>
        <rect y="8.5" width="28" height="3" fill="#8a8a8a"/>
        <rect y="16" width="28" height="3" fill="#8a8a8a"/>
      </svg>
      SEE THE MISSIONS
    </div>
    <div class="brand">HOPEWINGSRALLY</div>
    <nav class="auth">
      <a class="auth-btn login" href="#">LOGIN</a>
      <a class="auth-btn signup" href="#">SIGN UP</a>
    </nav>
  </header>

  <div class="hero-photo" role="img" aria-label="Black and white photograph of two hands holding each other"></div>

  <svg class="family-icon" viewBox="0 0 120 120" role="img" aria-label="Home icon">
    <path d="M10 56 L60 14 L110 56" fill="none" stroke="var(--line)" stroke-width="5" stroke-linejoin="round"/>
    <path d="M24 46 V110 H96 V46" fill="none" stroke="var(--line)" stroke-width="5"/>
    <rect x="50" y="72" width="20" height="38" fill="none" stroke="var(--line)" stroke-width="5"/>
  </svg>

  <section class="pledge">
    <p class="pledge-line">“ She has a <span class="gold">NAME</span>,</p>
    <p class="pledge-line">He Has a <span class="grey">DREAM</span>.</p>
    <p class="pledge-line">She Hopes She would</p>
    <p class="pledge-line">have a <span class="gold">FUTURE</span></p>
    <p class="pledge-punch">He is Like You<span class="close">”.</span></p>
    <p class="pledge-note">1 USD a month will help her and him</p>
  </section>

  <footer class="footer-strip">
    <span class="mark">©</span>
    <span>Copyright 2016, <a href="#">www.hopewingsrally.test</a></span>
  </footer>
  <div class="page-code">M1</div>
</body>
</html>
```